Orthobiologic, StemCell, Bone Marrow Aspirate Device Distributor

We need a wordpress fully functioning website design for an innovative ortho-biologic, Bone Marrow Aspirate Device that extracts stem cells for orthopedic regenerative medical professionals. We also offer state of the art training in there office setting with licensed medical staff, a full service support team, and software for tracking patient outcome over time. We are an innovative company that prides itself on gold standard support. We will have other offerings on our website and would like a spot for "future" products. We would like to see designs that look professional, medical, and convey support, security, science, and innovation. We prefer shades of blue and red/orange. I particularly like the following websites that also sell the same device in order of preference:regenacelltherapy.comhttps://aspire-medical.eu/marrow-cellution/https://www.matrixbiosurgical.com/#emerging-solutions-in-healthcareElite2elite.comI have attached a few pictures of the device for reference

Target Market(s)

Orthopedics, Regenerative medicine doctors, Industry representatives, Hospitals

Industry/Entity Type

Medical Equipment

Coding

Coded - Design and coding required

Colors
3176b5
33a6d7
f37022
ec1f27

Requirements
Must have
• It must be able to have videos which I can supply, email, online ordering, and sfax. I have a domain name Coralweavesolutions.com . It must have a FAQ section which you can obtain some information from https://www.tolvenclinical.com/solutions#resources
• The device is manufactured by Dulmor and this is the link to the product page http://www.dulmor.com/quintadraw
• I am currently working on a custom logo and should be able to supply that in short order. I prefer shades of blue and red.
Nice to have
• I would love to have a graphic video as seen here: please see quinta draw vs bone marrow aspirate concentrate.
• https://www.tolvenclinical.com/solutions#competition
• I would pay considerably more to have something similar if it is at all possible
Should not have
• Nothing specific

```html
<!DOCTYPE html>
<html lang="en">
<head>
<meta charset="utf-8">
<title>Coralweave Solutions — Our Products</title>
<link rel="stylesheet" href="https://fonts.googleapis.com/css2?family=Mulish:wght@300;400;500;600;700;800&display=swap">
<style>
  :root {
    --blue: #3176b5;
    --blue-light: #33a6d7;
    --blue-deep: #2a63ad;
    --orange: #f37022;
    --red: #ec1f27;
    --ink: #333333;
    --text: #555555;
    --muted: #6b6b6b;
    --footer-bg: #f0f0f0;
    --white: #ffffff;
  }
  * { box-sizing: border-box; margin: 0; padding: 0; }
  html, body { width: 1200px; height: 3300px; overflow: hidden; }
  body { font-family: "Mulish", sans-serif; color: var(--text); background: var(--white); position: relative; }

  .site-header { position: absolute; top: 0; left: 0; width: 1200px; height: 95px; background: var(--white); }
  .brand { position: absolute; left: 148px; top: 20px; color: var(--blue); font-weight: 800; line-height: 1; }
  .brand-name { font-size: 27px; letter-spacing: 0.5px; display: block; }
  .brand-sub { font-size: 21px; letter-spacing: 5px; font-weight: 800; display: block; margin-top: 3px; }
  .main-nav { position: absolute; top: 38px; left: 412px; display: flex; gap: 37px; font-size: 18px; color: #222; }

  .hero { position: absolute; top: 95px; left: 0; width: 1200px; height: 395px; background: #000; }
  .hero-art { position: absolute; left: 28px; top: 0; width: 1142px; height: 395px;
    background: radial-gradient(ellipse 260px 240px at 50% 55%, #e07a2a 0%, #b8442a 35%, #1f3d9a 70%, #0a0f2a 100%); }
  .hero-title { position: absolute; top: 150px; width: 1200px; text-align: center; color: var(--white); font-size: 46px; font-weight: 600; letter-spacing: 1px; }

  .intro { position: absolute; top: 490px; left: 0; width: 1200px; height: 372px; text-align: center; }
  .section-title { color: var(--blue); font-size: 32px; font-weight: 400; letter-spacing: 0.5px; }
  .intro .section-title { margin-top: 63px; }
  .intro p { width: 810px; margin: 22px auto 0; font-size: 18px; line-height: 27px; color: var(--text); }
  .intro .down-arrow { position: absolute; left: 588px; top: 258px; }

  .feature { position: absolute; top: 862px; left: 0; width: 1200px; height: 478px; background: linear-gradient(180deg, var(--blue-light) 0%, var(--blue-deep) 100%); }
  .feature-media { position: absolute; left: 153px; top: 96px; width: 440px; height: 274px;
    background: radial-gradient(ellipse 200px 110px at 50% 50%, #a3362a 0%, #6e1c16 55%, #2a1a14 100%); }
  .feature-body { position: absolute; left: 634px; top: 88px; width: 420px; color: var(--white); }
  .feature-body h2 { font-size: 32px; font-weight: 400; letter-spacing: 0.5px; margin-bottom: 24px; }
  .feature-body p { font-size: 15.5px; line-height: 21.5px; margin-bottom: 21px; }

  .advantages { position: absolute; top: 1340px; left: 0; width: 1200px; height: 523px;
    background: linear-gradient(90deg, #c8b48a 0%, #5a2a22 35%, #3a1416 70%, #1e0a12 100%); }
  .advantages-box { position: absolute; left: 268px; top: 75px; width: 668px; height: 366px;
    background: linear-gradient(135deg, rgba(243,112,34,0.95) 0%, rgba(236,31,39,0.9) 100%); color: var(--white); text-align: center; padding-top: 60px; }
  .advantages-box h2 { font-size: 32px; font-weight: 400; letter-spacing: 0.5px; }
  .advantages-box h3 { font-size: 19px; font-weight: 400; margin-top: 20px; }
  .advantages-box p { font-size: 16px; line-height: 27px; width: 590px; margin: 4px auto 0; }

  .benefits { position: absolute; top: 1863px; left: 0; width: 1200px; height: 1045px; }
  .benefits > .section-title { position: absolute; top: 52px; width: 1200px; text-align: center; color: var(--ink); font-size: 34px; }
  .benefit { position: absolute; width: 360px; }
  .benefit .tick { position: absolute; left: -44px; top: 0; }
  .benefit h4 { color: var(--blue); font-size: 17.5px; font-weight: 600; margin-bottom: 10px; }
  .benefit p { font-size: 13px; line-height: 17px; color: var(--muted); }
  .references { position: absolute; left: 196px; top: 737px; width: 820px; font-size: 13px; line-height: 19px; color: var(--muted); }
  .references p { margin-bottom: 19px; }

  .site-footer { position: absolute; top: 2908px; left: 0; width: 1200px; height: 392px; background: var(--footer-bg); }
  .footer-col { position: absolute; top: 80px; font-size: 15px; color: #444; }
  .footer-col h5 { font-size: 16px; font-weight: 800; color: #222; margin-bottom: 14px; letter-spacing: 0.2px; }
  .footer-col li { list-style: none; line-height: 27px; }
  .contact-item { display: flex; gap: 12px; align-items: flex-start; line-height: 17px; margin-bottom: 16px; }
  .social li { display: flex; align-items: center; gap: 12px; line-height: 34px; }
  .social .dot { width: 24px; height: 24px; border-radius: 50%; background: var(--blue); }
  .footer-bottom { position: absolute; top: 320px; left: 0; width: 1200px; border-top: 1px solid #d6d6d6; text-align: center; padding-top: 26px; font-size: 15px; color: #999; }
</style>
</head>
<body>

<header class="site-header">
  <div class="brand"><span class="brand-name">CORALWEAVE</span><span class="brand-sub">SOLUTIONS</span></div>
  <nav class="main-nav"><span>ABOUT</span><span>PRODUCTS</span><span>SERVICES</span><span>SOLUTION</span><span>NEWS</span><span>CONTACT</span></nav>
</header>

<section class="hero">
  <div class="hero-art" role="img" aria-label="Illuminated anatomical illustration of the pelvis and lower spine"></div>
  <h1 class="hero-title">OUR PRODUCTS</h1>
</section>

<section class="intro">
  <h2 class="section-title">QUINTA DRAW</h2>
  <p>maximizes stem &amp; progenitor cell recovery while minimizing peripheral blood infiltration. Because fluid under force follow the path of least resistance, traditional trocar needles with side ports aspirate primarily through the distal end of the cannula. This leads to excessive blood collection, requiring additional manipulation (i.e. centrifugation or chemical separation in a laboratory).</p>
  <svg class="down-arrow" width="24" height="52" viewBox="0 0 24 52" fill="none" stroke="#3176b5" stroke-width="2.5"><line x1="12" y1="1" x2="12" y2="49"/><polyline points="2,38 12,49 22,38"/></svg>
</section>

<section class="feature">
  <div class="feature-media" role="img" aria-label="Cutaway illustration of bone showing red marrow cells"></div>
  <div class="feature-body">
    <h2>QUINTA DRAW</h2>
    <p>accesses aspirate flow collected exclusively laterally as the tip of the aspiration cannula is closed, allowing marrow collection perpendicular to and around the channel created by the device. It incorporates technology to precisely reposition the harvesting cannula within the marrow space after each aspiration. These features achieve a clinicians' desire for a single entry point.</p>
    <p>QUINTA DRAWTM aspirates from multiple geographies while limiting peripheral blood collection.</p>
  </div>
</section>

<section class="advantages" role="img" aria-label="Illustration of a bone with marrow being aspirated">
  <div class="advantages-box">
    <h2>COMPETITIVE ADVANTAGES</h2>
    <h3>Quinta DrawTM Gives You More Cells</h3>
    <p>Marrow Stem cells heal tissue as an integral part of a patient's immune system and only marrow stem cells are powerful enough to reconstitute an entire immune system in an oncology setting.<br>The industry standard for measuring the number of stem cells from marrow for use in regenerative medicine is CFU-f (colony forming unit – fibroblast).</p>
  </div>
</section>

<section class="benefits">
  <h2 class="section-title">KEY BENEFITS</h2>

  <div class="benefit" style="left:242px; top:152px;">
    <svg class="tick" width="30" height="30" viewBox="0 0 30 30" fill="none" stroke="#f37022" stroke-width="2.5"><circle cx="15" cy="15" r="13"/><polyline points="9,15 13.5,19.5 21,10.5"/></svg>
    <h4>Reduce the Cost of Utilizing Biologics</h4>
    <p>The Quinta DrawTM System delivers a better regenerative solution (more stem cells) at a reduced cost compared to the industry leading solutions.</p>
  </div>
  <div class="benefit" style="left:674px; top:152px;">
    <svg class="tick" width="30" height="30" viewBox="0 0 30 30" fill="none" stroke="#f37022" stroke-width="2.5"><circle cx="15" cy="15" r="13"/><polyline points="9,15 13.5,19.5 21,10.5"/></svg>
    <h4>Minimize Sterility Challenges</h4>
    <p>Centrifugation systems require passing the BMA off the sterile field for processing and back on for implantation. The Quinta DrawTM System eliminates the additional steps where infection concerns must be managed.</p>
  </div>
  <div class="benefit" style="left:240px; top:300px;">
    <svg class="tick" width="30" height="30" viewBox="0 0 30 30" fill="none" stroke="#f37022" stroke-width="2.5"><circle cx="15" cy="15" r="13"/><polyline points="9,15 13.5,19.5 21,10.5"/></svg>
    <h4>Minimize O/R Time</h4>
    <p>Centrifugation systems typically required 20 minutes or more of spin time during the surgical procedure, not to mention the additional personnel (perfusion) and support time needed for preparation and cleanup of the equipment.</p>
  </div>
  <div class="benefit" style="left:672px; top:300px;">
    <svg class="tick" width="30" height="30" viewBox="0 0 30 30" fill="none" stroke="#f37022" stroke-width="2.5"><circle cx="15" cy="15" r="13"/><polyline points="9,15 13.5,19.5 21,10.5"/></svg>
    <h4>Minimize Sample Waste</h4>
    <p>Centrifugation systems typically discard 80% of the aspirate due to the high levels of peripheral blood. Worse, significant numbers of the desired cells (approx. 40%) are discarded because as these cells increase in density prior to division, they are processed into the undesired red cell centrifuge component and thus discarded, substantially limiting the regenerative potential of the resulting sample.</p>
  </div>
  <div class="benefit" style="left:240px; top:540px;">
    <svg class="tick" width="30" height="30" viewBox="0 0 30 30" fill="none" stroke="#f37022" stroke-width="2.5"><circle cx="15" cy="15" r="13"/><polyline points="9,15 13.5,19.5 21,10.5"/></svg>
    <h4>Minimize Use of Anti-Coagulants</h4>
    <p>Centrifugation systems require at least 10% dilution by volume for the addition of anti-coagulant to allow the sample to separate, and also require another 10% dilution in the form of a neutralizing agent such as thrombin and calcium chloride in order for the marrow to clot in the graft. The Quinta DrawTM System eliminates these requirements.</p>
  </div>
  <div class="benefit" style="left:672px; top:540px;">
    <svg class="tick" width="30" height="30" viewBox="0 0 30 30" fill="none" stroke="#f37022" stroke-width="2.5"><circle cx="15" cy="15" r="13"/><polyline points="9,15 13.5,19.5 21,10.5"/></svg>
    <h4>Eliminate the Need to Filter</h4>
    <p>Protocols require the marrow to be filtered prior to centrifugation. Cells bound within a cell aggregate can be delivered to the patient when mixed with graft material or injected. This is not the case when aggregates are filtered out prior to centrifugation. Filtering takes additional time, but more importantly, filtering reduces regenerative potential.</p>
  </div>

  <div class="references">
    <p>The Quinta DrawTM aspiration system that incorporates a Single puncture promoting only Lateral flow from Multiple sites (SSLM Method) produced concentrations of CFU-fs, CD34+ cells and CD117+ cells that were comparable or greater compared directly to centrifuged bone marrow concentrates (BMAC) from the same patient.</p>
    <p>Dr. Alan Verrick Professor of Biology, Chair of the Biology Department; Harlow University</p>
    <p>A larger-volume of aspirate (more than 2mL) from a given site is contraindicated with the additional volume contributing little to the overall number of bone-marrow cells and results principally in unnecessary blood loss.</p>
    <p>BRENHOLT R, et al "Aspiration to Obtain Osteoblast Progenitor Cells from Human Bone Marrow: The Influence of Aspiration Volume" The Journal of Skeletal Repair; VOL. 79-A, NO. 11 Westmere Clinic</p>
  </div>
</section>

<footer class="site-footer">
  <div class="footer-col" style="left:206px;">
    <h5>CONTACT US</h5>
    <div class="contact-item" style="margin-top:20px;"><svg width="16" height="20" viewBox="0 0 16 20" fill="none" stroke="#333" stroke-width="1.6"><path d="M8 19 C3 12 1.5 9.5 1.5 7 A6.5 6.5 0 0 1 14.5 7 C14.5 9.5 13 12 8 19Z"/><circle cx="8" cy="7" r="2.2"/></svg><span>482 Larkspur Avenue #B<br>Texas 75201 TX</span></div>
    <div class="contact-item"><svg width="16" height="16" viewBox="0 0 16 16" fill="none" stroke="#333" stroke-width="1.5"><path d="M3 1.5 L6 1.5 L7 5 L5 6.5 C6 8.5 7.5 10 9.5 11 L11 9 L14.5 10 L14.5 13 C14.5 14 13.5 14.5 12.5 14.5 C6.5 14 2 9.5 1.5 3.5 C1.5 2.5 2 1.5 3 1.5Z"/></svg><span>555.014.2287</span></div>
    <div class="contact-item"><svg width="16" height="14" viewBox="0 0 16 14" fill="none" stroke="#333" stroke-width="1.4"><rect x="1" y="1.5" width="14" height="11"/><polyline points="1,1.5 8,8 15,1.5"/></svg><span>info@coralweavesolutions.com</span></div>
  </div>
  <div class="footer-col" style="left:462px;">
    <h5>COMPANY</h5>
    <ul><li>Home</li><li>About us</li><li>Services</li><li>Products</li><li>Contact</li></ul>
  </div>
  <div class="footer-col" style="left:607px;">
    <h5>PRODUCTS</h5>
    <ul><li>Sed porta</li><li>Suspendisse quam</li><li>Leo molestie</li><li>Sed luctus</li><li>Fermentum</li></ul>
  </div>
  <div class="footer-col" style="left:787px;">
    <h5>RESOURCES</h5>
    <ul><li>FAQ</li><li>Videos</li><li>News</li><li>Contact Us</li></ul>
  </div>
  <div class="footer-col" style="left:951px;">
    <h5>GET IN TOUCH</h5>
    <ul class="social"><li><span class="dot"></span>Chirper</li><li><span class="dot"></span>Facepage</li><li><span class="dot"></span>Linkline</li><li><span class="dot"></span>Snapgram</li></ul>
  </div>
  <div class="footer-bottom">Copyright © 2019 All right reserved</div>
</footer>

</body>
</html>
```